Allied Health team of Physiotherapists & Occupational Therapists seek a business card design

We have our new logo, we now need our new business cards and stationary. Tidewell: Oedema & Family Clinic is seeking a generic card design to represent our whole team and individual cards for each therapist that incorporates our new logo to communicate our holistic approach that is calming, nuturing, supportive and welcoming.
Our Physiotherapists and Occupational Therapists assess, treat and provide education for people who are at risk of or who have lymphoedema. This is often as a result of treatment for cancer. We provide pre-operative and post-operative management and cancer rehabilitation in our Pilates studio. Our team also consists of Physiotherapists who have a strong interest in pelvic floor and continence management for both men and women.

Target Market(s)

Mainly women health conscious

Industry/Entity Type

Allied Health: Physiotherapy / Occupational Therapy

Contact Information for Business Card

Address: 14 Gallivant Ave Harrowby 3287 Phone: 84316570 fax: 8431 6578 Email: info@tidewellcareservices.com.au Website: tidewellcareservices.com.au Facebook address: facebook.com/TidewellOedemaAndFamilyCareClinic. Room to write appointments. Individual cards need to have name, office email and individual email and professional details

Requirements
Must have
• Logo as per uploaded documents

```html
<!DOCTYPE html>
<html lang="en">
<head>
<meta charset="utf-8">
<title>Tidewell: Oedema & Family Clinic – Business Cards</title>
<link rel="stylesheet" href="https://fonts.googleapis.com/css2?family=Montserrat:wght@400;500;600;700&display=swap">
<style>
  :root {
    --backdrop: #e6e8eb;
    --card: #ffffff;
    --peach: #f3ae8e;
    --orange: #e9895c;
    --grey: #7f8582;
    --sage: #a7b0a5;
    --rule: #d4d8d3;
    --swirl-a: #f7e6dc;
    --swirl-b: #eef0ec;
  }
  * { box-sizing: border-box; margin: 0; padding: 0; }
  html, body { width: 1200px; height: 1200px; overflow: hidden; }
  body {
    background: var(--backdrop);
    font-family: "Montserrat", sans-serif;
    position: relative;
  }
  .card {
    position: absolute;
    left: 150px;
    width: 900px;
    height: 515px;
    background: var(--card);
    border-radius: 14px;
    overflow: hidden;
    box-shadow: 0 6px 24px rgba(40, 50, 60, 0.12);
  }
  .card--front { top: 55px; }
  .card--back { top: 630px; }

  /* Brand lockup */
  .brand {
    position: absolute;
    display: flex;
    align-items: center;
    gap: 16px;
  }
  .brand__dot {
    width: 30px; height: 30px;
    border-radius: 50%;
    border: 3px solid currentColor;
    flex: none;
  }
  .brand__name {
    font-weight: 600;
    font-size: 25px;
    line-height: 1.25;
  }
  .card--front .brand { left: 60px; top: 200px; width: 340px; color: var(--orange); }

  .swirl {
    position: absolute;
    right: -40px; top: -30px;
    width: 420px; height: 260px;
    border-radius: 50%;
    background: radial-gradient(ellipse at 60% 40%, var(--swirl-a), var(--swirl-b) 55%, rgba(255,255,255,0) 72%);
  }

  .profile {
    position: absolute;
    left: 470px; top: 52px;
  }
  .profile__name {
    font-weight: 700;
    font-size: 38px;
    color: var(--grey);
    letter-spacing: -0.5px;
  }
  .profile__degree {
    font-weight: 600;
    font-size: 22px;
    color: var(--orange);
    margin-top: 6px;
  }
  .profile__cert {
    font-size: 17px;
    color: var(--orange);
    line-height: 1.3;
    margin-top: 4px;
  }
  .profile__role {
    font-weight: 700;
    font-size: 17px;
    color: var(--orange);
    margin-top: 4px;
  }

  .contact {
    position: absolute;
    left: 60px; bottom: 46px;
    font-size: 19px;
    line-height: 1.5;
    color: var(--grey);
    list-style: none;
  }
  .contact__key { color: var(--orange); font-weight: 600; margin-right: 4px; }
  .contact__gap { display: inline-block; width: 18px; }

  /* Back */
  .band {
    position: absolute;
    left: 0; top: 0; right: 0;
    height: 270px;
    background: var(--peach);
  }
  .card--back .brand { left: 50px; top: 96px; width: 330px; color: var(--card); }
  .social {
    position: absolute;
    left: 420px; top: 100px;
    color: var(--card);
    font-size: 19px;
    line-height: 1.55;
    font-weight: 500;
  }
  .appointments {
    position: absolute;
    left: 0; right: 0; top: 270px; bottom: 0;
    padding: 34px 80px 0;
  }
  .appointments__title {
    text-align: center;
    font-weight: 700;
    font-size: 26px;
    letter-spacing: 2px;
    color: var(--sage);
  }
  .appointments__line {
    height: 2px;
    background: var(--rule);
    margin-top: 54px;
  }
  .appointments__line + .appointments__line { margin-top: 56px; }
</style>
</head>
<body>
  <section class="card card--front" aria-label="Business card front">
    <div class="swirl" role="img" aria-label="Soft decorative leaf swirl"></div>
    <div class="brand">
      <span class="brand__dot"></span>
      <span class="brand__name">Tidewell: Oedema &amp; Family Clinic</span>
    </div>
    <div class="profile">
      <h1 class="profile__name">Miriam Holt</h1>
      <p class="profile__degree">B. Physio</p>
      <p class="profile__cert">Post Grad Cert. Continence &amp;<br>Pelvic Floor Rehabilitation</p>
      <p class="profile__role">Physiotherapist Pelvic Health</p>
    </div>
    <ul class="contact">
      <li><span class="contact__key">A:</span>14 Gallivant Ave, Harrowby 3287</li>
      <li><span class="contact__key">T:</span>8431 6570<span class="contact__gap"></span><span class="contact__key">F:</span>8431 6578</li>
      <li><span class="contact__key">E:</span>info@tidewellcareservices.com.au</li>
      <li><span class="contact__key">W:</span>tidewellcareservices.com.au</li>
    </ul>
  </section>

  <section class="card card--back" aria-label="Business card back">
    <div class="band"></div>
    <div class="brand">
      <span class="brand__dot"></span>
      <span class="brand__name">Tidewell: Oedema &amp; Family Clinic</span>
    </div>
    <div class="social">
      <p>facebook.com/TidewellOedema</p>
      <p>AndFamilyCareClinic</p>
      <p>tidewellcareservices.com.au</p>
    </div>
    <div class="appointments">
      <h2 class="appointments__title">APPOINTMENTS</h2>
      <div class="appointments__line"></div>
      <div class="appointments__line"></div>
    </div>
  </section>
</body>
</html>
```